Im want a website LIKE VRX's and FleetHollow.com's with product payment options like Trenzo's

I need a website LIKE VRX with a header made EXACTLY LIKE THAT OF FLEETHOLLOWS .

The front page photo should be like that of FLEETHOLLOW's webpage as well.

The name of the website will be called "M.K. (Caldera Key)".

We will be targeting ALL MARKETS in a small town in central Panama and charging businesses "listing fees" like a phone book does but also providing informational blogs, news, and other interesting activities.

THIS IS A MULTI PAGE WEBSITE

THIS IS WHERE VRX's website meets Brivelle/FleetHollow.

Once the layout is built I will tweak and modify, add information, and upload items for sale.

Here is a list of specific categories that should be listed out above the front page header image/search bar

-- Home -- News -- Travel -- Activities -- Shop & Dine -- Store -- More... --

These categories should be spread across the bottom of the page in three sections:

WHATS SO GREAT ABOUT (Caldera Key),
HAND PICKED TOURS
ACTIVITIES etc.

Also lets use www.Trenzo.example 's
"HOT DESTINATIONS"
"BEAT THE BEST PRICES IN BOQUETE"
"OCTOBERS INSIDER PICKS"
"TOP DESTINATIONS"
and spread them in four sections side-by-side near the bottom of the page.

Overall I would like to see the finished product to be something LIKE VRX's and FleetHollows.

WE NEED ONLINE PAYMENT OPTIONS LIKE BRIVELLE'S WEBSITE HAS

This will be a desktop website but should be very mobile friendly as well.

-rodmund

P.S. Good luck!

If it isn't already too late to change the website name, the name of the website should be "Caldera Key". Added Friday, October 9, 2015

What do you guys think the budget should be to win this? Added Saturday, October 10, 2015

www.palmorra.example is the most amazing simple site. Whoever can make me a replica with my specifications will win immediately!!!! Added Sunday, October 18, 2015

OMG www.palmorra.example is the bomb!So simple and elegant. Whoever can make me an EXACT REPLICA OF WWW.PALMORRA.EXAMPLE as my site with the specifications mentioned in my brief will take home the $825.00 immediately! Good luck amigos! Added Sunday, October 18, 2015

Does anybody know how to add recurring monthly billing options on this website? Added Sunday, October 18, 2015

ALL MARKETS

Product

Coded - Design and coding required

5+ page

• Coinvey payment options.
• I must be able to add and remove photos/text and video from the HTML files in the page.
• Be creative my friends, and may the odds be forever in your favor!
• I added some photos of a good layout for our page below.

```html
<!DOCTYPE html>
<html lang="en">
<head>
<meta charset="utf-8">
<title>Caldera Key</title>
<link href="https://fonts.googleapis.com/css2?family=Open+Sans:wght@400;600;700&family=Raleway:wght@600;700&display=swap" rel="stylesheet">
<style>
:root{
  --green:#35b98a;
  --green-dark:#2a9a72;
  --ink:#3b4650;
  --text:#6b737a;
  --muted:#9aa1a7;
  --line:#e3e6e8;
  --header:#3d4a55;
  --header-dark:#2f3b45;
  --footer:#2a3946;
  --footer-dark:#22303c;
  --page:#eceff1;
  --white:#fff;
  --star:#f5b631;
}
*{box-sizing:border-box;margin:0;padding:0}
html,body{width:1200px;height:2904px;overflow:hidden}
body{font-family:"Open Sans",Arial,sans-serif;color:var(--text);font-size:14px;background:var(--page);position:relative}
.backdrop{position:absolute;left:0;top:0;width:1200px;height:1300px;background:linear-gradient(180deg,#8fc7ec 0%,#b9dff2 22%,#d9eef3 38%,#7fc9c9 44%,#e9ddc3 52%,#efe6d4 70%,var(--page) 100%)}
.site{position:absolute;left:100px;top:20px;width:1000px;height:2440px;background:var(--white)}
.topbar{display:flex;height:100px;background:var(--header)}
.brand{width:160px;background:#2c6f62;color:#fff;padding:26px 18px;font-family:Raleway,sans-serif}
.brand b{display:block;font-size:17px;font-weight:700;letter-spacing:.5px}
.brand small{font-size:11px;color:#cfe9e1}
.topbar-right{flex:1;display:flex;align-items:center;padding:0 24px;color:#dfe5ea;font-size:13px;gap:22px}
.topbar-right .phone{flex:1;display:flex;align-items:center;gap:8px}
.btn{display:inline-block;background:var(--green);color:#fff;border:0;font-weight:600;font-size:12px;padding:8px 18px;text-transform:uppercase}
.btn.ghost{background:transparent;border:1px solid #7a8690;color:#dfe5ea}
.nav{height:48px;background:var(--header-dark);display:flex;align-items:center;padding:0 12px}
.nav a{color:#d5dde3;text-decoration:none;font-size:13px;padding:0 20px}
.nav a.active{color:#fff;font-weight:600}
.hero{position:relative;height:532px;background:linear-gradient(180deg,#c7ccd0 0%,#dfe3e5 28%,#8e9a8d 50%,#3f5a35 72%,#2b4326 100%)}
.hero .arrow{position:absolute;top:250px;width:30px;height:30px}
.tabs{display:flex;height:52px;background:var(--header)}
.tab{flex:1;display:flex;align-items:center;gap:10px;padding:0 24px;color:#d5dde3;font-size:12px;border-right:1px solid #4b5862}
.tab.active{background:var(--green);color:#fff}
.tab i{width:10px;height:10px;border-radius:50%;border:2px solid currentColor}
.search{display:flex;gap:24px;padding:28px 40px 0;align-items:flex-end;height:128px}
.field{flex:1}
.field label{display:block;font-size:12px;color:var(--ink);font-weight:600;margin-bottom:8px}
.field div{height:36px;border:1px solid var(--line);font-size:12px;color:var(--muted);padding:10px 12px}
.search .btn{height:36px;padding:10px 30px;flex:0 0 auto}
.welcome{text-align:center;padding:40px 60px 0;height:400px}
h2{font-family:Raleway,sans-serif;color:var(--ink);font-size:24px;font-weight:700}
.welcome p{margin:28px 0 24px;font-size:13px;line-height:22px;text-align:left}
.welcome .btn{padding:10px 30px}
.section-head{display:flex;align-items:center;justify-content:space-between;padding:0 0 0 0;border-bottom:1px solid var(--line);height:44px}
.section-head h2{border-bottom:3px solid var(--green);padding-bottom:10px;margin-bottom:-1px}
.hot{position:absolute;left:40px;top:1180px;width:920px}
.pager{display:flex;gap:6px}
.pager span{width:22px;height:22px;border-radius:50%;background:var(--green);display:block}
.cards{display:flex;gap:40px;margin-top:36px}
.card{flex:1}
.photo{position:relative;height:212px}
.price{position:absolute;right:0;bottom:0;background:var(--green);color:#fff;font-size:11px;padding:5px 12px}
.card h3,.feat h3{font-size:15px;color:var(--ink);font-weight:600;margin-top:16px}
.card h3 span,.feat h3 span{font-weight:400;color:var(--muted);font-size:12px;margin-left:8px}
.stars{color:var(--star);font-size:13px;letter-spacing:2px}
.card p{font-size:13px;line-height:21px;margin-top:12px}
.more{display:block;text-align:right;color:var(--green);font-size:12px;margin-top:20px}
.split{position:absolute;left:40px;top:1740px;width:920px;display:flex;gap:60px}
.split>div{flex:1}
.feat .photo{height:320px;margin-top:36px}
.feat p{font-size:13px;line-height:21px;margin-top:14px}
.quote{margin-top:36px;background:#f2f4f5;padding:24px;font-size:13px;line-height:21px;height:130px}
.rating{display:flex;justify-content:center;gap:12px;align-items:center;margin-top:22px;font-size:12px}
.person{position:relative;text-align:center;margin-top:18px}
.avatar{width:80px;height:80px;border-radius:50%;background:linear-gradient(135deg,#c9a58a,#7a5b48);margin:0 auto}
.person .name{color:var(--green);font-size:12px;margin-top:10px}
.person .role{font-size:11px;color:var(--muted)}
.person .side{position:absolute;top:24px;width:30px;height:30px;border-radius:50%;background:#d6dbdf}
footer{position:absolute;left:0;top:2510px;width:1200px;height:394px;background:var(--footer);color:#aeb9c2}
.cols{display:flex;gap:40px;padding:44px 100px 0;height:300px}
.cols>div{flex:1}
footer h4{font-family:Raleway,sans-serif;color:#fff;font-size:20px;margin-bottom:16px}
footer p{font-size:12px;line-height:19px}
.sub{display:flex;margin-top:14px}
.sub div{width:130px;height:30px;background:#fff;font-size:11px;color:var(--muted);padding:8px}
.sub span{width:34px;height:30px;background:var(--green)}
.news{display:flex;gap:10px;margin-bottom:14px}
.news i{width:56px;height:44px;background:#4d6070;flex:0 0 auto}
.tags{display:flex;flex-wrap:wrap;gap:6px}
.tags span{border:1px solid #55687a;font-size:11px;padding:4px 8px}
.social{display:flex;gap:10px;margin-top:14px}
.social i{width:22px;height:22px;border-radius:50%;border:1px solid #8d9aa5}
.bottom{position:absolute;left:0;bottom:0;width:1200px;height:94px;background:var(--footer-dark);display:flex;align-items:center;padding:0 100px}
.bottom nav a{color:#aeb9c2;font-size:12px;text-decoration:none;margin-right:28px}
.bottom small{position:absolute;left:100px;bottom:16px;font-size:11px}
.bottom .btn{margin-left:auto;padding:12px 30px}
.up{position:absolute;left:585px;top:-16px;width:30px;height:30px;background:var(--green);border-radius:50%}
</style>
</head>
<body>
<div class="backdrop" role="img" aria-label="Tropical beach with blue sky and sea"></div>

<div class="site">
  <header class="topbar">
    <div class="brand"><b>CALDERA KEY</b><small>Enjoy the calm</small></div>
    <div class="topbar-right">
      <div class="phone">
        <svg width="14" height="14" viewBox="0 0 24 24"><path fill="#35b98a" d="M6.6 10.8a15 15 0 0 0 6.6 6.6l2.2-2.2c.3-.3.7-.4 1-.2 1.1.4 2.3.6 3.6.6.6 0 1 .4 1 1V20c0 .6-.4 1-1 1A17 17 0 0 1 3 4c0-.6.4-1 1-1h3.5c.6 0 1 .4 1 1 0 1.3.2 2.5.6 3.6.1.3 0 .7-.2 1z"/></svg>
        Call us +507 555 0142
      </div>
      <span>Log in</span><span>English</span>
      <span class="btn">Login</span><span class="btn ghost">Register</span>
    </div>
  </header>
  <nav class="nav">
    <a class="active">Home</a><a>Features</a><a>About Us</a><a>Gallery</a><a>Blog</a><a>Packages</a><a>Contact Us</a>
  </nav>
  <section class="hero" role="img" aria-label="Misty forested mountain under clouds">
    <svg class="arrow" style="left:20px" viewBox="0 0 30 30"><path d="M19 6 10 15l9 9" stroke="#fff" stroke-width="3" fill="none"/></svg>
    <svg class="arrow" style="right:20px" viewBox="0 0 30 30"><path d="m11 6 9 9-9 9" stroke="#fff" stroke-width="3" fill="none"/></svg>
  </section>
  <div class="tabs">
    <div class="tab active"><i></i>Search Destination</div>
    <div class="tab"><i></i>Search Hotels</div>
    <div class="tab"><i></i>Popular Locations</div>
    <div class="tab"><i></i>Nightlife Locations</div>
  </div>
  <form class="search">
    <div class="field"><label>Your Name</label><div>Enter name</div></div>
    <div class="field"><label>Select Date</label><div>dd / mm / yyyy</div></div>
    <div class="field"><label>Destination</label><div>Enter destination</div></div>
    <span class="btn">Let's Find</span>
  </form>
  <section class="welcome">
    <h2>Welcome To Our Site</h2>
    <p>Caldera Key is a small town in central Panama full of cool mountain air, coffee farms, rivers and friendly local businesses. Here you will find listings for places to stay, eat and shop, along with travel news, helpful blogs and a calendar of the best activities around town. Browse by category, plan your next day out, compare prices and book directly with local guides and shops. Whether you are visiting for a weekend or settling in for a season, our guide helps you discover hidden trails, waterfalls, markets and restaurants that make this valley so special to everyone who visits.</p>
    <span class="btn">Read More</span>
  </section>

  <section class="hot">
    <div class="section-head"><h2>Hot Destinations</h2><div class="pager"><span></span><span></span></div></div>
    <div class="cards">
      <article class="card">
        <div class="photo" role="img" aria-label="Town park with trees and lawn" style="background:linear-gradient(180deg,#9fb6c8,#6f8b5a 60%,#4d6a3b)"><span class="price">Per Day $39</span></div>
        <h3>Lorem Ipsum<span>Central America</span></h3>
        <div class="stars">★★★★★ <small style="color:#9aa1a7;letter-spacing:0">420 Reviews</small></div>
        <p>Enjoy the valley views with a guided walk, local lunch and a visit to the town plaza.</p>
        <span class="more">Show details »</span>
      </article>
      <article class="card">
        <div class="photo" role="img" aria-label="Old stone tower against blue sky" style="background:linear-gradient(180deg,#8db8e0,#b7c7cf 55%,#6d6a5c)"><span class="price">Per Day $45</span></div>
        <h3>Lorem Ipsum<span>Central America</span></h3>
        <div class="stars">★★★★★ <small style="color:#9aa1a7;letter-spacing:0">318 Reviews</small></div>
        <p>Explore historic ruins and old town streets with a friendly guide and fresh coffee.</p>
        <span class="more">Show details »</span>
      </article>
      <article class="card">
        <div class="photo" role="img" aria-label="Lush jungle trail" style="background:linear-gradient(180deg,#7e9b62,#4f6e3a 55%,#354d28)"><span class="price">Per Day $52</span></div>
        <h3>Lorem Ipsum<span>Central America</span></h3>
        <div class="stars">★★★★★ <small style="color:#9aa1a7;letter-spacing:0">256 Reviews</small></div>
        <p>Hike green forest trails to hidden waterfalls and watch birds along the river banks.</p>
        <span class="more">Show details »</span>
      </article>
    </div>
  </section>

  <section class="split">
    <div class="feat">
      <div class="section-head"><h2>Featured Places</h2></div>
      <div class="photo" role="img" aria-label="Canal locks with a ship and green hills" style="background:linear-gradient(180deg,#b9cfdf,#8fa9a8 40%,#6c8a7e 70%,#4f6a5c)"><span class="price">Business Class $1200</span></div>
      <h3>Lorem Ipsum<span>by Caldera Key Travel</span> <span class="stars" style="margin-left:10px">★★★★★</span></h3>
      <p>We have a number of different tours within our guide that specialise in different areas of business so you can be sure that you won't receive a generic service and although we won't boast years and years of service we can ensure you that is a good thing in this industry.</p>
      <span class="more">Show details »</span>
    </div>
    <div>
      <div class="section-head"><h2>Client Testimonials</h2></div>
      <div class="quote">Our stay was relaxed and easy from the first click. Booking was simple, payments were secure and every local guide we met was kind, punctual and full of stories about the town and the valley around it.</div>
      <div class="rating"><span>5 stars</span><span class="stars">★★★★★</span></div>
      <div class="person">
        <span class="side" style="left:0"></span><span class="side" style="right:0"></span>
        <div class="avatar" role="img" aria-label="Guest portrait"></div>
        <div class="name">Jonathan Doe</div>
        <div class="role">Happy Traveller</div>
      </div>
    </div>
  </section>
</div>

<footer>
  <div class="cols">
    <div>
      <h4>Newsletter</h4>
      <p>Sign up for local news, new listings and special offers sent to your inbox once a month.</p>
      <div class="sub"><div>Email Here</div><span></span></div>
    </div>
    <div>
      <h4>Latest News</h4>
      <div class="news"><i></i><p>Coffee harvest festival opens this weekend<br><small>2 days ago</small></p></div>
      <div class="news"><i></i><p>New river trail map now online<br><small>5 days ago</small></p></div>
    </div>
    <div>
      <h4>Tags</h4>
      <div class="tags"><span>Travel</span><span>Adventure</span><span>Hotels</span><span>Dine</span><span>Shops</span><span>Coffee</span><span>Tours</span><span>Nature</span><span>Events</span><span>News</span></div>
    </div>
    <div>
      <h4>Address</h4>
      <p>18 Calle Mirador<br>Caldera Key, Chiriquí<br>Panama<br>Phone: +507 555 0142<br>Email: hello@calderakey.example</p>
      <div class="social"><i></i><i></i><i></i><i></i></div>
    </div>
  </div>
  <div class="bottom">
    <span class="up"></span>
    <nav><a>Home</a><a>Features</a><a>About Us</a><a>Gallery</a><a>Blog</a><a>Packages</a><a>Contact Us</a></nav>
    <small>Copyright © Caldera Key. All rights reserved.</small>
    <span class="btn">Billing Program</span>
  </div>
</footer>
</body>
</html>
```